holloway paving service

Needs to have phone number 0418259730 and email markholloway@brightmail.com.au.
ABN 62318470915
name mark holloway

For all your concreting solutions
Excavation
Exposed & colour concrete
House & shed slabs
Driveways
Landing & steps

Contact Information for Business Card

ph 0418259730
email markholloway@brightmail.com.au.
ABN 62318470915
name mark holloway

```html
<!DOCTYPE html>
<html lang="en">
<head>
<meta charset="utf-8">
<title>Holloway Paving Service – Business Card</title>
<link href="https://fonts.googleapis.com/css2?family=Montserrat:wght@600&family=Lato:wght@400;700&display=swap" rel="stylesheet">
<style>
  :root {
    --backdrop: #ece7e1;
    --kraft-light: #d6b28a;
    --kraft: #c79d70;
    --kraft-dark: #b88a5c;
    --ink: #141210;
  }
  * { box-sizing: border-box; margin: 0; padding: 0; }
  html, body {
    width: 1200px;
    height: 900px;
    overflow: hidden;
    background: var(--backdrop);
  }
  .canvas { position: relative; width: 1200px; height: 900px; }
  .card {
    position: absolute;
    background: linear-gradient(160deg, var(--kraft-light) 0%, var(--kraft) 55%, var(--kraft-dark) 100%);
    color: var(--ink);
  }
  .card--front { left: 330px; top: 90px; width: 556px; height: 344px; }
  .card--back  { left: 330px; top: 470px; width: 558px; height: 342px; text-align: center; }

  .brand-mark {
    position: absolute;
    left: 93px; top: 131px;
    width: 80px; height: 80px;
    background: var(--ink);
  }
  .brand-divider {
    position: absolute;
    left: 198px; top: 118px;
    width: 2px; height: 110px;
    background: var(--ink);
  }
  .brand-lockup {
    position: absolute;
    left: 210px; top: 140px;
    width: 270px;
    font-family: "Montserrat", sans-serif;
    font-weight: 600;
    font-size: 19px;
    line-height: 22px;
    text-transform: uppercase;
    text-align: center;
  }
  .brand-lockup__rule-row {
    display: flex; align-items: center; gap: 10px;
    letter-spacing: 3px;
  }
  .brand-lockup__rule { flex: 1; height: 2px; background: var(--ink); }
  .brand-phone {
    position: absolute;
    left: 210px; top: 183px;
    width: 270px;
    font-family: "Montserrat", sans-serif;
    font-size: 16px;
    letter-spacing: 2.5px;
    text-align: center;
  }

  .contact-name {
    position: absolute; left: 0; right: 0; top: 63px;
    font-family: "Montserrat", sans-serif; font-weight: 600; font-size: 19px;
    text-transform: uppercase;
  }
  .contact-line {
    position: absolute; left: 0; right: 0;
    font-family: "Lato", sans-serif; font-size: 15px;
  }
  .contact-line--abn { top: 104px; }
  .contact-line--email { top: 140px; }
  .contact-divider {
    position: absolute; left: 144px; top: 185px;
    width: 270px; height: 1px; background: var(--ink);
  }
  .services-heading {
    position: absolute; left: 0; right: 0; top: 209px;
    font-family: "Lato", sans-serif; font-weight: 700; font-size: 15.5px;
    text-transform: uppercase;
  }
  .services-list {
    position: absolute; left: 0; right: 0; top: 236px;
    font-family: "Lato", sans-serif; font-size: 15px; line-height: 20px;
  }
</style>
</head>
<body>
<main class="canvas">
  <section class="card card--front" aria-label="Card front">
    <div class="brand-mark"></div>
    <div class="brand-divider"></div>
    <div class="brand-lockup">
      <div>Holloway Paving</div>
      <div class="brand-lockup__rule-row">
        <span class="brand-lockup__rule"></span><span>Service</span><span class="brand-lockup__rule"></span>
      </div>
    </div>
    <div class="brand-phone">0418259730</div>
  </section>

  <section class="card card--back" aria-label="Card back">
    <h1 class="contact-name">Mark Holloway</h1>
    <p class="contact-line contact-line--abn">ABN 62318470915</p>
    <p class="contact-line contact-line--email">markholloway@brightmail.com.au</p>
    <div class="contact-divider"></div>
    <h2 class="services-heading">For all your concreting solutions</h2>
    <p class="services-list">
      Excavation &nbsp;&nbsp;| &nbsp;Exposed &amp; colour concrete<br>
      House &amp; shed slabs &nbsp;| Driveways | Landing &amp; steps
    </p>
  </section>
</main>
</body>
</html>
```